Online Dating Website called WinkAtWheel.com

PLEASE CAN ALL PARTICIPATING DESIGNERS PLEASE SUBMIT ALL PAGES AS DETAILED IN THE ORIGINAL BRIEF BELOW WITHIN 48 HOURS TO AVOID WINKATWHEEL EXTENDING THE CONTEST FURTHER.

We have an online dating website that is 95% fully functional and now require an exciting and creative designer to help us create the best dating experience. We are looking for your ideas on a couple of our key pages. These are our landing, profile and search page. We already have a homepage that we are happy with and winning designers will look to build upon the foundations of the homepage and extend them through their designs.

The premise of the site is the idea that if you've ever seen someone out driving and wished you could communicate because you found them attractive, how would you? Well with WinkAtWheel.com you can. Just enter their vehicle registration number (license plate) in to the website in order to get in touch, flirt and develop a relationship. It also allows users to find each other based on other criteria. It acts as both a specialist service and a normal dating website.

The pages that require developing are 1) our landing page, this is the page users see when they first login to the site, it comprises various pieces of information but it's primary function is a live feed of events generated based on the users favourited profiles and interactions with the user. 2) The profile page is the page where users can edit their own information, given the nature of this page we are looking for a creative design that gives this page some flair. 3) Finally we are looking for ideas for our search page, this page needs to provide a list of users who meet the user's search requirements and display the profile of a selected user.
Updates

Project Deadline Extended
Reason: We've asked for certain pages in our brief to be designed and this still hasn't been done. We've contacted the designers that have currently submitted designs and requested this several times. We still await for this to happen.

Target Market(s)

Male or Female age 18+

Industry/Entity Type

Dating

Requirements
Must have
• Our must have feature is a designer with an open mind. The functionality of the site must be present, all we ask is for you to be creative with the layout. Think out side of the box, change the colours, the layout, and the background as you feel. Make it look current and appealing to the user.
Nice to have
• Theme's carried through from the home page
Should not have
• Do not include Comic Sans or Times New Roman font in your designs.

```html
<!DOCTYPE html>
<html lang="en">
<head>
<meta charset="utf-8">
<title>WinkAtWheel – Live Feed</title>
<link href="https://fonts.googleapis.com/css2?family=Source+Sans+3:wght@400;600;700&display=swap" rel="stylesheet">
<style>
:root{
  --bar-dark:#1f2022;
  --bar-dark-2:#2d2e31;
  --sky-top:#8fd2f8;
  --sky-bottom:#5bb9ef;
  --pink:#ec5f9f;
  --pink-dark:#d8437f;
  --grey-head:#9a9b9d;
  --grey-head-dark:#7b7c7e;
  --dark-head:#3e3f41;
  --dark-head-2:#202123;
  --light-head:#cfd0d2;
  --panel:#ffffff;
  --panel-soft:#efefef;
  --line:#d9d9d9;
  --text:#444;
  --text-soft:#666;
  --link:#1f7fc7;
  --blue-btn:#3a9be0;
  --grey-btn:#8d8e90;
  --tick:#3fae49;
  --nav:#9fd8ff;
  --nav-pink:#f06aa6;
}
*{box-sizing:border-box;margin:0;padding:0}
html,body{width:1200px;height:2296px;overflow:hidden}
body{font-family:"Source Sans 3",Arial,sans-serif;color:var(--text);
  background:linear-gradient(180deg,var(--sky-top) 86px,var(--sky-bottom) 1200px,#7fcaf3 2130px);position:relative}
.site-header{height:86px;background:linear-gradient(180deg,var(--bar-dark-2),var(--bar-dark));display:flex;align-items:center;justify-content:space-between;padding:0 102px 0 96px}
.brand{display:flex;align-items:center;gap:10px;color:#fff;font-size:33px;font-weight:400;letter-spacing:.2px}
.brand-dot{width:26px;height:26px;border-radius:50%;background:var(--pink)}
.main-nav{display:flex;gap:12px;font-size:15px;align-items:center}
.main-nav a{color:var(--nav);text-decoration:none}
.main-nav a.current{color:#fff}
.main-nav a.accent{color:var(--nav-pink)}
.main-nav .sep{color:#777;font-size:12px}
.hero{text-align:center;color:#fff;padding-top:27px}
.hero h1{font-size:31px;font-weight:700;line-height:1.2}
.hero p{font-size:22px;font-weight:600;line-height:34px;margin-top:6px}
.columns{position:absolute;top:252px;left:100px;display:flex;gap:8px}
.panel{background:var(--panel);padding:5px;height:1862px;border-radius:3px}
.col-left{width:244px}
.col-feed{width:495px}
.col-right{width:243px}
.pink-head{height:41px;border-radius:3px;background:linear-gradient(180deg,#f279b2,var(--pink-dark));color:#fff;font-size:19px;font-weight:700;display:flex;align-items:center;justify-content:space-between;padding:0 20px}
.chev{width:0;height:0;border-left:8px solid transparent;border-right:8px solid transparent;border-top:9px solid #fff}
.profile-meta{text-align:center;font-size:14px;padding:10px 0 9px}
.photo{height:147px;border-radius:2px}
.field{height:34px;border:1px solid var(--line);background:#fff;display:flex;align-items:center;justify-content:space-between;padding-left:14px;font-size:14px;color:#888;margin-top:7px}
.btn{background:linear-gradient(180deg,#a5a6a8,var(--grey-btn));color:#fff;font-size:13px;font-weight:700;letter-spacing:.5px;padding:0 12px;height:100%;display:flex;align-items:center}
.select-arrow{width:0;height:0;border-left:7px solid transparent;border-right:7px solid transparent;border-top:8px solid #999;margin-right:14px}
.pair{display:flex;gap:8px;margin-top:10px}
.pair .blue{flex:1;height:33px;background:linear-gradient(180deg,#5bb3ef,#2f8ad4);color:#fff;font-size:14px;font-weight:700;display:flex;align-items:center;justify-content:center;gap:8px;border-radius:2px}
.gap{height:14px}
.search-btn{display:flex;justify-content:flex-end;margin-top:9px}
.search-btn .btn{height:30px;border-radius:2px}
.stat-box{background:var(--panel-soft);margin-top:5px;padding:0 18px}
.stat-group{border-bottom:1px solid #d6d6d6;padding:12px 0 10px}
.stat-group:last-child{border-bottom:0}
.stat-group h3{font-size:16px;font-weight:700;color:#333;margin-bottom:4px}
.stat-row{display:flex;justify-content:space-between;font-size:13px;line-height:23px;color:#555}
.stat-row b{font-weight:700;color:#555}
.fav-list{background:var(--panel-soft);margin-top:10px;padding:10px 12px;height:432px;border:1px solid #e0e0e0}
.fav{display:flex;gap:14px;margin-bottom:20px}
.fav-pic{width:96px;height:65px;border:2px solid #fff;flex:none}
.fav-info{font-size:13px;line-height:19px;color:#666}
.fav-info strong{display:block;font-size:15px;color:#444}
.feed-item{margin-bottom:13px}
.feed-head{height:43px;border-radius:3px;display:flex;align-items:center;justify-content:space-between;padding:0 12px 0 20px;color:#fff;font-size:16px;font-weight:600}
.feed-head small{font-size:13px;font-weight:600}
.feed-head.status{background:linear-gradient(180deg,#b0b1b3,var(--grey-head-dark))}
.feed-head.update{background:linear-gradient(180deg,#4b4c4e,var(--dark-head-2))}
.feed-head.view{background:linear-gradient(180deg,#e3e4e5,#c4c5c7);color:#444}
.feed-body{background:var(--panel-soft);border:1px solid #e2e2e2;margin-top:4px;height:96px;display:flex;align-items:center;gap:18px;padding:0 12px}
.feed-pic{width:93px;height:64px;flex:none;border:2px solid #fff}
.feed-body p{font-size:13px;line-height:21px;color:#666}
.match-list{list-style:none;padding:14px 8px 6px 12px}
.match-list li{display:flex;align-items:center;gap:10px;height:31px;font-size:12px;color:#555}
.match-list li b{color:var(--link);font-size:14px;font-weight:700}
.people{display:grid;grid-template-columns:93px 93px;gap:0 24px;padding:12px 0 0 15px}
.person{text-align:center;margin-bottom:18px}
.person .pic{height:89px;border:2px solid #e3e3e3}
.person p{font-size:14px;line-height:19px;margin-top:6px;color:#555}
.person p b{color:var(--link);font-weight:600}
.backgrounds{display:grid;grid-template-columns:93px 93px;gap:10px 10px;padding:12px 0 0 19px}
.backgrounds div{height:64px;border:1px solid #ddd}
.bg-note{text-align:right;font-size:13px;padding:16px 16px 0 0;color:#555}
.chat-tab{position:absolute;left:1141px;top:1875px;width:59px;height:181px;background:linear-gradient(90deg,#3a3b3d,#222);border-radius:4px 0 0 4px;color:#fff;display:flex;flex-direction:column;align-items:center;justify-content:center;gap:14px}
.chat-tab span{writing-mode:vertical-rl;transform:rotate(180deg);font-weight:700;font-size:19px;letter-spacing:.5px}
.site-footer{position:absolute;left:0;top:2133px;width:1200px;height:163px;background:linear-gradient(180deg,var(--bar-dark-2),var(--bar-dark));display:flex;padding:28px 0 0 100px;color:#ddd}
.foot-col{list-style:none;font-size:14px;line-height:29px;margin-right:0}
.foot-col li::before{content:"» ";color:#fff}
.foot-col:nth-child(1){width:148px}
.foot-col:nth-child(2){width:209px}
.foot-col:nth-child(3){width:300px}
.foot-brand{margin-left:auto;padding-right:102px;text-align:right;font-size:14px;line-height:22px}
.foot-brand .brand{justify-content:flex-end;font-size:33px;margin-bottom:4px}
.socials{display:flex;gap:12px;position:absolute;left:722px;top:88px}
.socials i{display:block;width:35px;height:35px;border-radius:3px}
</style>
</head>
<body>
<header class="site-header">
  <div class="brand">winkatwheel<span class="brand-dot"></span></div>
  <nav class="main-nav">
    <a class="current">Home</a><span class="sep">::</span>
    <a>Profile</a><span class="sep">::</span>
    <a>Messages</a><span class="sep">::</span>
    <a>Matches</a><span class="sep">::</span>
    <a>Search</a><span class="sep">::</span>
    <a class="accent">Support</a><span class="sep">::</span>
    <a class="accent">My Account</a>
  </nav>
</header>

<section class="hero">
  <h1>Welcome to WinkAtWheel</h1>
  <p>Donec ut nibh a sapien accumsan placerat ac porttitor enim. Mauris non imperdiet est,<br>sed feugiat sapien. Mauris ut aliquet lorem, nec vehicula massa.</p>
</section>

<main class="columns">
  <aside class="panel col-left">
    <div class="pink-head">Lee</div>
    <div class="profile-meta">(24 years old - Castleford)</div>
    <div class="photo" role="img" aria-label="Member profile photo" style="background:linear-gradient(135deg,#c9b29a,#8a7464 60%,#5d5048)"></div>
    <div class="field">How are you?<span class="btn">UPDATE</span></div>
    <div class="pair">
      <div class="blue"><svg width="14" height="14" viewBox="0 0 14 14"><circle cx="7" cy="4" r="3.2" fill="#fff"/><path d="M1 14c0-4 2.7-6 6-6s6 2 6 6z" fill="#fff"/></svg>PROFILE</div>
      <div class="blue"><svg width="18" height="14" viewBox="0 0 18 14"><rect x="0" y="3" width="18" height="11" rx="2" fill="#fff"/><rect x="6" y="0" width="6" height="4" fill="#fff"/><circle cx="9" cy="8.5" r="3.2" fill="#2f8ad4"/></svg>UPLOAD</div>
    </div>
    <div class="gap"></div>
    <div class="pink-head">Seen Someone?</div>
    <div class="field" style="margin-top:8px">Search Reg</div>
    <div class="field">Make<span class="select-arrow"></span></div>
    <div class="field">Colour<span class="select-arrow"></span></div>
    <div class="search-btn"><span class="btn">SEARCH</span></div>
    <div class="gap" style="height:12px"></div>
    <div class="pink-head">your Status<span class="chev"></span></div>
    <div class="stat-box">
      <div class="stat-group"><h3>Like 124</h3>
        <div class="stat-row">Image you have Liked<b>32</b></div>
        <div class="stat-row">Status you have Liked<b>67</b></div>
        <div class="stat-row">Likes on your images<b>20</b></div>
        <div class="stat-row">Likes on your Status<b>55</b></div></div>
      <div class="stat-group"><h3>Messages 171</h3>
        <div class="stat-row">Image you have Liked<b>32</b></div>
        <div class="stat-row">Status you have Liked<b>67</b></div></div>
      <div class="stat-group"><h3>Favourites 20</h3>
        <div class="stat-row">Image you have Liked<b>32</b></div>
        <div class="stat-row">Status you have Liked<b>67</b></div></div>
    </div>
    <div class="gap" style="height:16px"></div>
    <div class="pink-head">Feed Filter<span class="chev"></span></div>
    <div class="stat-box">
      <div class="stat-group"><h3>Like 124</h3>
        <div class="stat-row">Image you have Liked<svg width="12" height="10"><path d="M1 5l3.5 3.5L11 1.5" stroke="var(--tick)" stroke-width="2.2" fill="none"/></svg></div>
        <div class="stat-row">Status you have Liked<svg width="12" height="10"><path d="M1 5l3.5 3.5L11 1.5" stroke="var(--tick)" stroke-width="2.2" fill="none"/></svg></div>
        <div class="stat-row">Likes on your images<svg width="12" height="10"><path d="M1 5l3.5 3.5L11 1.5" stroke="var(--tick)" stroke-width="2.2" fill="none"/></svg></div>
        <div class="stat-row">Likes on your Status<svg width="12" height="10"><path d="M1 5l3.5 3.5L11 1.5" stroke="var(--tick)" stroke-width="2.2" fill="none"/></svg></div></div>
      <div class="stat-group"><h3>Messages 171</h3>
        <div class="stat-row">Image you have Liked<svg width="12" height="10"><path d="M1 5l3.5 3.5L11 1.5" stroke="var(--tick)" stroke-width="2.2" fill="none"/></svg></div>
        <div class="stat-row">Status you have Liked<svg width="12" height="10"><path d="M1 5l3.5 3.5L11 1.5" stroke="var(--tick)" stroke-width="2.2" fill="none"/></svg></div></div>
      <div class="stat-group"><h3>Favourites 20</h3>
        <div class="stat-row">Image you have Liked<svg width="12" height="10"><path d="M1 5l3.5 3.5L11 1.5" stroke="var(--tick)" stroke-width="2.2" fill="none"/></svg></div>
        <div class="stat-row">Status you have Liked<svg width="12" height="10"><path d="M1 5l3.5 3.5L11 1.5" stroke="var(--tick)" stroke-width="2.2" fill="none"/></svg></div></div>
    </div>
    <div class="gap" style="height:16px"></div>
    <div class="pink-head">Your Favourites<span class="chev"></span></div>
    <div class="field" style="margin-top:8px">Type a name...<span class="btn">UPDATE</span></div>
    <div class="fav-list">
      <div class="fav"><div class="fav-pic" role="img" aria-label="Favourite member photo" style="background:linear-gradient(135deg,#b7cfa4,#2c2c2c)"></div><div class="fav-info"><strong>Jenny</strong>22 year old<br>Leeds</div></div>
      <div class="fav"><div class="fav-pic" role="img" aria-label="Favourite member photo" style="background:linear-gradient(135deg,#c9c3e6,#5d4f8e)"></div><div class="fav-info"><strong>Jenny</strong>22 year old<br>Leeds</div></div>
      <div class="fav"><div class="fav-pic" role="img" aria-label="Favourite member photo" style="background:linear-gradient(135deg,#dff2fa,#1d8fc0)"></div><div class="fav-info"><strong>Jenny</strong>22 year old<br>Leeds</div></div>
      <div class="fav"><div class="fav-pic" role="img" aria-label="Favourite member photo" style="background:linear-gradient(135deg,#a8c37a,#4f6a2f)"></div><div class="fav-info"><strong>Jenny</strong>22 year old<br>Leeds</div></div>
      <div class="fav"><div class="fav-pic" role="img" aria-label="Favourite member photo" style="background:linear-gradient(135deg,#f2f4f7,#b9c3cf)"></div><div class="fav-info"><strong>Jenny</strong>22 year old<br>Leeds</div></div>
    </div>
  </aside>

  <section class="panel col-feed" aria-label="Live feed">
    <article class="feed-item"><div class="feed-head status"><span>Lee changed her status &nbsp;- <small>Tuesday 22 : 56</small></span><svg width="22" height="20" viewBox="0 0 22 20"><path d="M11 19L2.5 10.5A5 5 0 0 1 11 3.5a5 5 0 0 1 8.5 7z" fill="#4a4a4a"/></svg></div>
      <div class="feed-body"><div class="feed-pic" role="img" aria-label="Member photo" style="background:linear-gradient(135deg,#b7cfa4,#2c2c2c)"></div><p>Cum sociis natoque penatibus et magnis dis parturient montes, nascetur ridiculus mus. In sollicitudin id velit ac euismod. Donec vulputate, felis sit amet blandit rhoncus</p></div></article>
    <article class="feed-item"><div class="feed-head status"><span>Lee changed her status &nbsp;- <small>Tuesday 22 : 56</small></span><svg width="22" height="20" viewBox="0 0 22 20"><path d="M11 19L2.5 10.5A5 5 0 0 1 11 3.5a5 5 0 0 1 8.5 7z" fill="#4a4a4a"/></svg></div>
      <div class="feed-body"><div class="feed-pic" role="img" aria-label="Member photo" style="background:linear-gradient(135deg,#b7cfa4,#2c2c2c)"></div><p>Cum sociis natoque penatibus et magnis dis parturient montes, nascetur ridiculus mus. In sollicitudin id velit ac euismod. Donec vulputate, felis sit amet blandit rhoncus</p></div></article>
    <article class="feed-item"><div class="feed-head status"><span>Lee changed her status &nbsp;- <small>Tuesday 22 : 56</small></span><svg width="22" height="20" viewBox="0 0 22 20"><path d="M11 19L2.5 10.5A5 5 0 0 1 11 3.5a5 5 0 0 1 8.5 7z" fill="#4a4a4a"/></svg></div>
      <div class="feed-body"><div class="feed-pic" role="img" aria-label="Member photo" style="background:linear-gradient(135deg,#b7cfa4,#2c2c2c)"></div><p>Cum sociis natoque penatibus et magnis dis parturient montes, nascetur ridiculus mus. In sollicitudin id velit ac euismod. Donec vulputate, felis sit amet blandit rhoncus</p></div></article>
    <article class="feed-item"><div class="feed-head status"><span>Lee changed her status &nbsp;- <small>Tuesday 22 : 56</small></span><svg width="22" height="20" viewBox="0 0 22 20"><path d="M11 19L2.5 10.5A5 5 0 0 1 11 3.5a5 5 0 0 1 8.5 7z" fill="#4a4a4a"/></svg></div>
      <div class="feed-body"><div class="feed-pic" role="img" aria-label="Member photo" style="background:linear-gradient(135deg,#b7cfa4,#2c2c2c)"></div><p>Cum sociis natoque penatibus et magnis dis parturient montes, nascetur ridiculus mus. In sollicitudin id velit ac euismod. Donec vulputate, felis sit amet blandit rhoncus</p></div></article>
    <article class="feed-item"><div class="feed-head status"><span>Lee changed her status &nbsp;- <small>Tuesday 22 : 56</small></span><svg width="22" height="20" viewBox="0 0 22 20"><path d="M11 19L2.5 10.5A5 5 0 0 1 11 3.5a5 5 0 0 1 8.5 7z" fill="#4a4a4a"/></svg></div>
      <div class="feed-body"><div class="feed-pic" role="img" aria-label="Member photo" style="background:linear-gradient(135deg,#b7cfa4,#2c2c2c)"></div><p>Cum sociis natoque penatibus et magnis dis parturient montes, nascetur ridiculus mus. In sollicitudin id velit ac euismod. Donec vulputate, felis sit amet blandit rhoncus</p></div></article>
    <article class="feed-item"><div class="feed-head update"><span>Lee update her Profile &nbsp;- <small>Tuesday 22 : 56</small></span><svg width="36" height="20" viewBox="0 0 36 20"><ellipse cx="18" cy="10" rx="17" ry="9" fill="#0e0e0e"/><ellipse cx="18" cy="10" rx="12" ry="6" fill="#ddd"/><circle cx="18" cy="10" r="4" fill="#111"/></svg></div>
      <div class="feed-body"><div class="feed-pic" role="img" aria-label="Member photo" style="background:linear-gradient(135deg,#b7cfa4,#2c2c2c)"></div><p>Cum sociis natoque penatibus et magnis dis parturient montes, nascetur ridiculus mus. In sollicitudin id velit ac euismod. Donec vulputate, felis sit amet blandit rhoncus</p></div></article>
    <article class="feed-item"><div class="feed-head update"><span>Lee update her Profile &nbsp;- <small>Tuesday 22 : 56</small></span><svg width="36" height="20" viewBox="0 0 36 20"><ellipse cx="18" cy="10" rx="17" ry="9" fill="#0e0e0e"/><ellipse cx="18" cy="10" rx="12" ry="6" fill="#ddd"/><circle cx="18" cy="10" r="4" fill="#111"/></svg></div>
      <div class="feed-body"><div class="feed-pic" role="img" aria-label="Member photo" style="background:linear-gradient(135deg,#b7cfa4,#2c2c2c)"></div><p>Cum sociis natoque penatibus et magnis dis parturient montes, nascetur ridiculus mus. In sollicitudin id velit ac euismod. Donec vulputate, felis sit amet blandit rhoncus</p></div></article>
    <article class="feed-item"><div class="feed-head update"><span>Lee update her Profile &nbsp;- <small>Tuesday 22 : 56</small></span><svg width="36" height="20" viewBox="0 0 36 20"><ellipse cx="18" cy="10" rx="17" ry="9" fill="#0e0e0e"/><ellipse cx="18" cy="10" rx="12" ry="6" fill="#ddd"/><circle cx="18" cy="10" r="4" fill="#111"/></svg></div>
      <div class="feed-body"><div class="feed-pic" role="img" aria-label="Member photo" style="background:linear-gradient(135deg,#b7cfa4,#2c2c2c)"></div><p>Cum sociis natoque penatibus et magnis dis parturient montes, nascetur ridiculus mus. In sollicitudin id velit ac euismod. Donec vulputate, felis sit amet blandit rhoncus</p></div></article>
    <article class="feed-item"><div class="feed-head update"><span>Lee update her Profile &nbsp;- <small>Tuesday 22 : 56</small></span><svg width="36" height="20" viewBox="0 0 36 20"><ellipse cx="18" cy="10" rx="17" ry="9" fill="#0e0e0e"/><ellipse cx="18" cy="10" rx="12" ry="6" fill="#ddd"/><circle cx="18" cy="10" r="4" fill="#111"/></svg></div>
      <div class="feed-body"><div class="feed-pic" role="img" aria-label="Member photo" style="background:linear-gradient(135deg,#b7cfa4,#2c2c2c)"></div><p>Cum sociis natoque penatibus et magnis dis parturient montes, nascetur ridiculus mus. In sollicitudin id velit ac euismod. Donec vulputate, felis sit amet blandit rhoncus</p></div></article>
    <article class="feed-item"><div class="feed-head view"><span>WAW viewed your Profile &nbsp;- <small>Tuesday 22 : 56</small></span></div>
      <div class="feed-body"><div class="feed-pic" role="img" aria-label="Space scene image" style="background:radial-gradient(circle at 70% 30%,#f3c25a,#8a4a12 45%,#140c06 75%)"></div><p>Cum sociis natoque penatibus et magnis dis parturient montes, nascetur ridiculus mus. In sollicitudin id velit ac euismod. Donec vulputate, felis sit amet blandit rhoncus</p></div></article>
    <article class="feed-item"><div class="feed-head view"><span>WAW viewed your Profile &nbsp;- <small>Tuesday 22 : 56</small></span></div>
      <div class="feed-body"><div class="feed-pic" role="img" aria-label="Motocross rider image" style="background:linear-gradient(180deg,#d8dde2,#8f969c)"></div><p>Cum sociis natoque penatibus et magnis dis parturient montes, nascetur ridiculus mus. In sollicitudin id velit ac euismod. Donec vulputate, felis sit amet blandit rhoncus</p></div></article>
  </section>

  <aside class="panel col-right">
    <div class="pink-head">Your Matches</div>
    <ul class="match-list">
      <li><svg width="20" height="15" viewBox="0 0 20 15"><rect y="3" width="20" height="12" rx="2" fill="#888"/><rect x="6" width="8" height="4" fill="#888"/><circle cx="10" cy="9" r="3.5" fill="#fff"/></svg><b>WAW</b>has uploaded a new image</li>
      <li><svg width="20" height="15" viewBox="0 0 20 15"><rect y="3" width="20" height="12" rx="2" fill="#888"/><rect x="6" width="8" height="4" fill="#888"/><circle cx="10" cy="9" r="3.5" fill="#fff"/></svg><b>WAW</b>has uploaded a new image</li>
      <li><svg width="20" height="15" viewBox="0 0 20 15"><rect y="3" width="20" height="12" rx="2" fill="#888"/><rect x="6" width="8" height="4" fill="#888"/><circle cx="10" cy="9" r="3.5" fill="#fff"/></svg><b>WAW</b>has uploaded a new image</li>
      <li><svg width="20" height="15" viewBox="0 0 20 15"><ellipse cx="10" cy="6.5" rx="9" ry="6" fill="#888"/><path d="M4 10l-2 5 6-3z" fill="#888"/></svg><b>WAW</b>has uploaded a new image</li>
      <li><svg width="20" height="15" viewBox="0 0 20 15"><ellipse cx="10" cy="6.5" rx="9" ry="6" fill="#888"/><path d="M4 10l-2 5 6-3z" fill="#888"/></svg><b>WAW</b>has uploaded a new image</li>
      <li><svg width="20" height="15" viewBox="0 0 20 15"><rect y="3" width="20" height="12" rx="2" fill="#888"/><rect x="6" width="8" height="4" fill="#888"/><circle cx="10" cy="9" r="3.5" fill="#fff"/></svg><b>WAW</b>has uploaded a new image</li>
      <li><svg width="20" height="15" viewBox="0 0 20 15"><rect y="3" width="20" height="12" rx="2" fill="#888"/><rect x="6" width="8" height="4" fill="#888"/><circle cx="10" cy="9" r="3.5" fill="#fff"/></svg><b>WAW</b>has uploaded a new image</li>
    </ul>
    <div class="people">
      <div class="person"><div class="pic" role="img" aria-label="Match photo" style="background:linear-gradient(180deg,#eef1f4,#c9b39b)"></div><p><b>John</b> (26)<br>New york</p></div>
      <div class="person"><div class="pic" role="img" aria-label="Match photo" style="background:linear-gradient(180deg,#c7d2dc,#6b5547)"></div><p><b>John</b> (26)<br>New york</p></div>
      <div class="person"><div class="pic" role="img" aria-label="Match photo" style="background:linear-gradient(180deg,#e9e2cf,#d9b67c)"></div><p><b>John</b> (26)<br>New york</p></div>
      <div class="person"><div class="pic" role="img" aria-label="Match photo" style="background:linear-gradient(180deg,#f1f1f1,#2a2a2a)"></div><p><b>John</b> (26)<br>New york</p></div>
      <div class="person"><div class="pic" role="img" aria-label="Match photo" style="background:linear-gradient(180deg,#6a3b2a,#c48a6d)"></div><p><b>John</b> (26)<br>New york</p></div>
      <div class="person"><div class="pic" role="img" aria-label="Match photo" style="background:linear-gradient(180deg,#5a4a6a,#d8d4cc)"></div><p><b>John</b> (26)<br>New york</p></div>
    </div>
    <div class="pink-head" style="margin-top:8px">Your Matches</div>
    <div class="backgrounds">
      <div role="img" aria-label="Background option: green leaves" style="background:linear-gradient(135deg,#2f4d1e,#8fae55)"></div>
      <div role="img" aria-label="Background option: sky and grass" style="background:linear-gradient(180deg,#4a9fe0,#bfe1f7 60%,#6fae3a)"></div>
      <div role="img" aria-label="Background option: rocky coast" style="background:linear-gradient(180deg,#5c9ad6,#c79c5e)"></div>
      <div role="img" aria-label="Background option: pale green" style="background:linear-gradient(135deg,#f2f7ea,#a7cf7f)"></div>
      <div role="img" aria-label="Background option: white flower" style="background:linear-gradient(135deg,#9fc9d9,#f0f4f2)"></div>
      <div role="img" aria-label="Background option: warm sunset" style="background:linear-gradient(135deg,#7a3a2a,#e7a46a)"></div>
      <div role="img" aria-label="Background option: blue light burst" style="background:radial-gradient(circle,#ffffff,#4b8fe0 45%,#173e8c)"></div>
      <div role="img" aria-label="Background option: golden field" style="background:linear-gradient(180deg,#f6d66a,#d8901f)"></div>
    </div>
    <div class="bg-note">Default Background</div>
  </aside>
</main>

<div class="chat-tab"><span>OPEN CHAT</span><svg width="26" height="22" viewBox="0 0 26 22"><rect x="6" y="0" width="20" height="13" rx="3" fill="#bbb"/><rect x="0" y="5" width="19" height="12" rx="3" fill="#fff"/><path d="M4 16l-2 6 7-5z" fill="#fff"/></svg></div>

<footer class="site-footer">
  <ul class="foot-col"><li>Home</li><li>Mobile Site</li><li>Circlely</li><li>Chatterly</li></ul>
  <ul class="foot-col"><li>General Conditions</li><li>Terms &amp; Conditions</li><li>Privacy Statement</li><li>Cookies Information</li></ul>
  <ul class="foot-col"><li>Contact us</li><li>FAQ's &amp; Help</li><li>Safe Dating Advice</li><li>Pricing Details</li></ul>
  <div class="socials"><i style="background:#3b5b9a"></i><i style="background:#3fb4e6"></i><i style="background:#1a78b4"></i></div>
  <div class="foot-brand">
    <div class="brand">winkatwheel<span class="brand-dot"></span></div>
    Copyright © 2013 &nbsp;Wink At Wheel<br>All rights reserved.
  </div>
</footer>
</body>
</html>
```